Amani Home Ltd retailer needs a web page design

We need a web page design for a new homeware and accessories store based in Johannesburg, South Africa. Our store carries modern African inspired items from designers that support social development and poverty alleviation initiatives. We have a particular preference for outfits that are centred on the empowerment of women.

Our business celebrates the skill, design and product of African craft and the work of designers looking to take that forward in a socially beneficial way (creating employment, developing skills, supporting local crafts people etc). We aim to carry items and inspirations from all over the African continent.

We would like to see a design that communicates African beauty and elegance without the typical tribal references that are made in reference to African craft or art.

We would like the web page to be stylish, uncomplicated, modern, captivating and appealing to the discerning customer. A similar value proposition is that of http://www.marlowtenwick.example/.

This is an e-commerce website which must be attractive to both individual buyers and design professionals so the website needs to look professional.

Here are links to some websites we like:
http://www.quenbyhollis.example/
http://www.dravelo.example/

Our logo is attached to the brief.

Target Market(s)

Our target market is female, age 20-50. However should not alienate the design conscious male customer therefore

Industry/Entity Type

E-Commerce

Requirements
Must have
• - A featured product banner which includes a photograph and text. This should be easy to edit as we will be changing the featured product regularly
- An easily expendable products section with categories. Examples of categories could be cushions, bedding, crockery etc. Should be easy to add new categories as well as new product pictures
- Home/landing page should be uncluttered
- Should use the logo and should be easy to change the logo which we have in various colour combinations. We plan to change the logo colours depending on circumstance e.g. make it red and white around Valentines day (similar to the way Vintrel frequently changes the logo on their landing page)

```html
<!DOCTYPE html>
<html lang="en">
<head>
<meta charset="utf-8">
<title>Amani Home — Homeware &amp; Accessories</title>
<link rel="stylesheet" href="https://fonts.googleapis.com/css2?family=Open+Sans:wght@400;600&family=Montserrat:wght@600&display=swap">
<style>
:root{
  --cream:#fcf7dc;
  --cream-box:#fdf9e3;
  --ink:#3b3b3b;
  --brown-top:#8a5a32;
  --brown-bottom:#5e3a1c;
  --green:#3e9b3f;
  --green-dark:#2f8431;
  --leaf:#8cc63f;
  --footer:#2f2f2f;
  --footer-base:#262626;
  --footer-text:#d6d6d6;
  --muted:#9a9a9a;
  --navy:#1d4e6b;
}
*{box-sizing:border-box;margin:0;padding:0}
html,body{width:1095px;height:1200px;overflow:hidden}
body{position:relative;background:var(--cream);font-family:'Open Sans',Arial,sans-serif;color:var(--ink)}
.abs{position:absolute}

.account{left:99px;top:86px;font-size:12.5px;letter-spacing:.3px;color:#444}
.account span{margin:0 8px}
.cart{right:92px;top:30px;display:flex;align-items:center;gap:9px;font-size:12px;color:#555}
.search{left:833px;top:69px;width:170px;height:29px;background:#fff;border:1px solid #ddd;border-radius:2px;display:flex;align-items:center;font-size:12px;color:#aaa;padding-left:9px}
.search .divider{position:absolute;left:141px;top:5px;width:1px;height:18px;background:#ddd}
.search svg{position:absolute;right:6px;top:6px}

.nav{left:90px;top:125px;width:915px;height:49px;background:linear-gradient(var(--brown-top),var(--brown-bottom));box-shadow:0 2px 3px rgba(0,0,0,.2)}
.nav a{position:absolute;top:16px;transform:translateX(-50%);color:#fff;text-decoration:none;font-size:13px;letter-spacing:.3px;white-space:nowrap}

.brand{left:468px;top:0;width:159px;height:199px;background:var(--cream-box);box-shadow:0 1px 4px rgba(0,0,0,.18);display:flex;flex-direction:column;align-items:center}
.brand-mark{margin-top:22px;width:74px;height:74px;background:var(--green)}
.brand-name{margin-top:30px;font-family:'Montserrat','Open Sans',sans-serif;font-weight:600;font-size:19px;letter-spacing:1.5px;color:var(--green)}
.brand-tagline{margin-top:3px;font-size:7px;letter-spacing:.6px;color:var(--navy)}

.hero{left:90px;top:183px;width:915px;height:448px;background:linear-gradient(110deg,#b98d5a 0%,#c9743b 28%,#5a5f7a 48%,#c7652c 66%,#6f8aa6 82%,#c2a274 100%)}
.arrow{width:33px;height:33px;border-radius:50%;background:rgba(40,40,40,.7);top:391px}
.arrow svg{display:block;margin:8px auto}
.hero-caption{left:115px;top:571px;height:44px;padding:0 8px;background:rgba(40,30,20,.75);color:#fff;font-weight:600;font-size:29px;line-height:44px;letter-spacing:.3px}

.tile{top:658px;width:296px;height:231px}
.tile .photo{height:185px}
.tile .label{height:46px;background:linear-gradient(var(--green),var(--green-dark));color:#fff;font-weight:600;font-size:19px;line-height:46px;padding-left:14px;letter-spacing:.2px}

.footer{left:0;top:915px;width:1095px;height:229px;background:var(--footer)}
.footer h3{position:absolute;top:22px;font-weight:400;font-size:16px;color:var(--leaf)}
.footer ul{position:absolute;top:57px;list-style:none;font-size:12.5px;color:var(--footer-text);line-height:23px}
.signup-text{left:592px;top:57px;width:230px;font-size:12.5px;line-height:17px;color:#bbb}
.field{left:592px;width:224px;height:25px;background:#eee;border-radius:3px;font-size:11.5px;color:#555;padding-left:13px;line-height:25px}
.subscribe{left:729px;top:167px;width:86px;height:26px;background:linear-gradient(#6fb42f,#4c8f1d);color:#fff;font-size:11.5px;text-align:center;line-height:26px;border-radius:2px}
.social li{display:flex;align-items:center;gap:13px;height:30px;font-size:12.5px;color:var(--footer-text)}
.social .dot{width:25px;height:25px;border-radius:50%;background:#f2f2f2}
.base{left:0;top:1144px;width:1095px;height:56px;background:var(--footer-base);text-align:center;line-height:56px;font-size:11.5px;color:var(--muted)}
</style>
</head>
<body>

<div class="abs account">REGISTER<span>/</span>LOGIN</div>

<div class="abs cart">0 items in your cart
  <svg width="28" height="24" viewBox="0 0 28 24"><path d="M8 9 L14 2 L20 9" fill="none" stroke="var(--navy)" stroke-width="2"/><rect x="1" y="9" width="26" height="3" fill="var(--navy)"/><path d="M3 12 H25 L23 23 H5 Z" fill="var(--navy)"/></svg>
</div>

<div class="abs search">Search<span class="divider"></span>
  <svg width="17" height="17" viewBox="0 0 17 17"><circle cx="7" cy="7" r="5.5" fill="none" stroke="#777" stroke-width="2"/><line x1="11" y1="11" x2="16" y2="16" stroke="#777" stroke-width="2.4"/></svg>
</div>

<nav class="abs nav">
  <a style="left:64px">HOME</a>
  <a style="left:173px">ABOUT US</a>
  <a style="left:297px">PRODUCTS</a>
  <a style="left:611px">ACCESSORIES</a>
  <a style="left:752px">CONTACT&nbsp; US</a>
  <a style="left:868px">GIFTS</a>
</nav>

<div class="abs brand">
  <div class="brand-mark"></div>
  <div class="brand-name">AMANI HOME</div>
  <div class="brand-tagline">homeware &amp; accessories</div>
</div>

<section class="abs hero" role="img" aria-label="Featured product photo: colourful woven rugs hanging on a sunlit clay wall"></section>
<div class="abs arrow" style="left:111px"><svg width="12" height="16" viewBox="0 0 12 16"><path d="M9 2 L3 8 L9 14" fill="none" stroke="#fff" stroke-width="3"/></svg></div>
<div class="abs arrow" style="left:950px"><svg width="12" height="16" viewBox="0 0 12 16"><path d="M3 2 L9 8 L3 14" fill="none" stroke="#fff" stroke-width="3"/></svg></div>
<div class="abs hero-caption">SED SED ULTRICIES PURUS</div>

<div class="abs tile" style="left:91px">
  <div class="photo" role="img" aria-label="Orange cast-iron teapot on a table" style="background:linear-gradient(160deg,#2c4a6e,#c9661b 55%,#8a5a20)"></div>
  <div class="label">AFRICAN PRODUCTS</div>
</div>
<div class="abs tile" style="left:400px">
  <div class="photo" role="img" aria-label="Model wearing a gold chain necklace" style="background:radial-gradient(circle at 50% 45%,#3e8f8a,#0f4a4c 75%)"></div>
  <div class="label">AFRICAN ACCESSORIES</div>
</div>
<div class="abs tile" style="left:708px">
  <div class="photo" role="img" aria-label="Colourful beaded collar close-up" style="background:linear-gradient(135deg,#3a3a3a,#c7472a 35%,#e0c22a 55%,#2f7fbf 75%,#555)"></div>
  <div class="label">LATEST OFFERS</div>
</div>

<footer class="abs footer">
  <h3 style="left:107px">Quick Links</h3>
  <ul style="left:108px"><li>Home</li><li>About us</li><li>Products</li><li>Accessories</li><li>Contact us</li><li>Gifts</li></ul>
  <h3 style="left:266px">Support Links</h3>
  <ul style="left:268px"><li>Clients</li><li>Partners</li><li>Testimonials</li><li>Jobs</li><li>Categories</li></ul>
  <h3 style="left:428px">Support Links</h3>
  <ul style="left:430px"><li>Press</li><li>Legal Notice</li><li>Privacy Policy</li><li>Term of Use</li></ul>
  <h3 style="left:590px">Newsletters Sign Up</h3>
  <p class="abs signup-text">Sign up for our daily email by entering your information below</p>
  <div class="abs field" style="top:102px">Your name</div>
  <div class="abs field" style="top:133px">Email address</div>
  <div class="abs subscribe">SUBSCRIBE</div>
  <h3 style="left:870px">Connect With Us</h3>
  <ul class="social" style="left:870px;top:65px;line-height:normal">
    <li><span class="dot"></span>Friendspace</li>
    <li><span class="dot"></span>Chirpline</li>
    <li><span class="dot"></span>Workcircle</li>
  </ul>
</footer>
<div class="abs base">Copyright &nbsp;©&nbsp; 2014 &nbsp;&nbsp;Amani Home Ltd. &nbsp;&nbsp;All rights reserved.</div>

</body>
</html>
```